VFX Company Business Card Design Project

The Kestrel Works is a decentralized Visual Effects Studio servicing the television and feature film industries.
Project Brief:
Take our logo that was previously designed on Pencil Harbor and make a double sided business card.
Requirements:
- Card MUST be double sided.
- Front of card MUST have the yellow part of our logo against the dark grey background.
- Back of card is completely up to the designer.
- Back of card must include the complete company logo.
Please follow these File Preparation guidelines:
http://printnook.ca/infopage?file=filetype_en&s=PrintNook_new&lang=en
Business

```html
<!DOCTYPE html>
<html lang="en">
<head>
<meta charset="utf-8">
<title>The Kestrel Works – Business Card</title>
<link rel="stylesheet" href="https://fonts.googleapis.com/css2?family=Asap:wght@400;500;600&display=swap">
<style>
  :root {
    --backdrop: #c9d2d6;
    --card-grey: #3a3a3b;
    --brand-yellow: #fbc51c;
    --text-light: #f2f2f2;
    --text-soft: #d6d6d6;
  }
  * { box-sizing: border-box; margin: 0; padding: 0; }
  html, body {
    width: 1200px;
    height: 960px;
    overflow: hidden;
    background: var(--backdrop);
    font-family: "Asap", sans-serif;
  }
  .sheet {
    width: 1200px;
    height: 960px;
    display: flex;
    flex-direction: column;
    align-items: center;
    justify-content: center;
    gap: 60px;
  }
  .card {
    position: relative;
    width: 630px;
    height: 360px;
    background: var(--card-grey);
    border-radius: 4px;
    box-shadow: 0 10px 30px rgba(0, 0, 0, 0.25);
    overflow: hidden;
  }

  /* Contact side */
  .card-contact .brand-name {
    position: absolute;
    left: 48px;
    top: 52px;
    color: var(--brand-yellow);
    font-weight: 600;
    font-size: 44px;
    letter-spacing: 0.5px;
  }
  .card-contact .person {
    position: absolute;
    left: 48px;
    top: 214px;
    color: var(--text-light);
    white-space: nowrap;
  }
  .person-name {
    font-size: 26px;
    font-weight: 500;
    letter-spacing: 0.5px;
  }
  .person-role {
    font-size: 15px;
    margin-left: 2px;
  }
  .contact-line {
    position: absolute;
    left: 48px;
    right: 48px;
    top: 270px;
    color: var(--text-soft);
    font-size: 15px;
    white-space: nowrap;
  }
  .contact-rule {
    position: absolute;
    left: 48px;
    right: 48px;
    top: 298px;
    height: 2px;
    background: var(--brand-yellow);
  }
  .address-line {
    position: absolute;
    left: 48px;
    right: 48px;
    top: 310px;
    color: var(--text-soft);
    font-size: 15px;
    white-space: nowrap;
  }

  /* Brand side */
  .card-brand .brand-mark {
    position: absolute;
    left: 40px;
    top: 34px;
    display: flex;
    align-items: center;
    gap: 14px;
  }
  .brand-dot {
    width: 22px;
    height: 22px;
    border-radius: 50%;
    background: var(--brand-yellow);
  }
  .brand-mark .brand-name {
    color: var(--brand-yellow);
    font-weight: 600;
    font-size: 30px;
  }
  .card-brand .brand-feature {
    position: absolute;
    right: 36px;
    bottom: 30px;
    color: var(--brand-yellow);
    font-weight: 600;
    font-size: 58px;
    line-height: 1;
    text-align: right;
  }
</style>
</head>
<body>
  <main class="sheet">
    <section class="card card-contact" aria-label="Business card, contact side">
      <div class="brand-name">The Kestrel Works</div>
      <div class="person">
        <span class="person-name">JANE MARLOW</span>
        <span class="person-role">Managing Partner</span>
      </div>
      <p class="contact-line">T: (480) 555-0142 | E: name@kestrelworks.com | www.kestrelworks.com</p>
      <div class="contact-rule"></div>
      <p class="address-line">4820 West Harbor Lane, Suite 210, Tempe, Arizona 85001</p>
    </section>

    <section class="card card-brand" aria-label="Business card, brand side">
      <div class="brand-mark">
        <span class="brand-dot"></span>
        <span class="brand-name">The Kestrel Works</span>
      </div>
      <div class="brand-feature">The Kestrel<br>Works</div>
    </section>
  </main>
</body>
</html>
```